Business Card Design Project

After recently finishing a design project for the company logo using markbazaar, it's now time for a business card. Attached to this is the logo.

The requirements for the business card are pretty straightforward:

- A clean, uncomplicated look
- Consistent usage of fonts
- Designs for both single sided and double sided cards
- A modern layout with preferably space to refer to social media accounts and/or downloadable vcards through a qr code
- consistent application of the company colour scheme: red/white. Hex codes for exact colour can be provided

Thanks!

```html
<!DOCTYPE html>
<html lang="en">
<head>
<meta charset="utf-8">
<title>Kestrel Hiring – Business Card</title>
<link rel="stylesheet" href="https://fonts.googleapis.com/css2?family=Source+Sans+3:wght@400;600&display=swap">
<style>
  :root {
    --page-bg: #e9e6e2;
    --card-bg: #231f20;
    --brand-red: #e41e26;
    --text-white: #ffffff;
    --text-grey: #8a8a8a;
  }
  * { margin: 0; padding: 0; box-sizing: border-box; }
  html, body {
    width: 960px;
    height: 1200px;
    overflow: hidden;
    background: var(--page-bg);
    font-family: "Source Sans 3", "Myriad Pro", Arial, sans-serif;
  }
  .canvas { position: relative; width: 960px; height: 1200px; }
  .card {
    position: absolute;
    left: 55px;
    width: 840px;
    height: 480px;
    background: var(--card-bg);
    border-radius: 30px;
    color: var(--text-white);
  }
  .card--front { top: 72px; }
  .card--back { top: 638px; }

  .wordmark {
    position: absolute;
    display: flex;
    align-items: center;
    gap: 26px;
    font-weight: 600;
    line-height: 1;
    color: var(--text-white);
    white-space: nowrap;
  }
  .wordmark__square { background: var(--brand-red); flex: none; }
  .card--front .wordmark { left: 140px; top: 80px; font-size: 80px; }
  .card--front .wordmark__square { width: 96px; height: 96px; }
  .card--back .wordmark { left: 0; right: 0; top: 200px; justify-content: center; font-size: 56px; }
  .card--back .wordmark__square { width: 66px; height: 66px; }

  .holder { position: absolute; right: 37px; top: 306px; text-align: right; }
  .holder__name { font-size: 26px; font-weight: 600; line-height: 32px; }
  .holder__role { font-size: 20px; line-height: 28px; }

  .contact { position: absolute; font-size: 20px; line-height: 28px; }
  .contact__line { display: flex; align-items: center; gap: 8px; white-space: nowrap; }
  .contact__icon { width: 14px; height: 14px; fill: var(--text-white); flex: none; }
  .contact--phone { left: 37px; top: 436px; }
  .contact--web { left: 259px; top: 402px; }
  .contact--address { right: 29px; top: 408px; text-align: right; }
</style>
</head>
<body>
<main class="canvas">
  <section class="card card--front" aria-label="Card front">
    <div class="wordmark"><span class="wordmark__square"></span>Kestrel Hiring</div>

    <div class="holder">
      <p class="holder__name">Your Name</p>
      <p class="holder__role">Designation</p>
    </div>

    <div class="contact contact--phone">
      <p class="contact__line">
        <svg class="contact__icon" viewBox="0 0 16 16" aria-hidden="true"><path d="M1 6c0-2 3-3 7-3s7 1 7 3v1h-4V5.5H5V7H1zM4 8h8l2 6H2z"/></svg>
        123-123-1234
      </p>
    </div>

    <div class="contact contact--web">
      <p class="contact__line">
        <svg class="contact__icon" viewBox="0 0 16 16" aria-hidden="true"><path d="M1 3h14v10H1z M2 4v.5l6 4.5 6-4.5V4z" fill-rule="evenodd"/></svg>
        info@yourwebsite.com
      </p>
      <p class="contact__line">
        <svg class="contact__icon" viewBox="0 0 16 16" aria-hidden="true"><circle cx="8" cy="8" r="6"/></svg>
        www.kestrelhiring.com
      </p>
    </div>

    <div class="contact contact--address">
      <p>1234, Street Name</p>
      <p>District, City, Country Code.</p>
    </div>
  </section>

  <section class="card card--back" aria-label="Card back">
    <div class="wordmark"><span class="wordmark__square"></span>Kestrel Hiring</div>
  </section>
</main>
</body>
</html>
```